Redesign of business card for Cedar Ridge Mechanical

We are looking for a new design for our business cards for Cedar Ridge Mechanical. We are a plumbing & HVAC construction company, operating on the West Coast of Canada and USA. Logo attached.
Industry/Entity Type
Construction - Plumbing & HVAC
Contact Information for Business Card
Name, address, phone numbers, email, website address
Look and feel
Each slider illustrates characteristics of the customer's brand and the style your logo design should communicate.

```html
<!DOCTYPE html>
<html lang="en">
<head>
<meta charset="utf-8">
<title>Cedar Ridge Mechanical – Business Card</title>
<link rel="stylesheet" href="https://fonts.googleapis.com/css2?family=Poppins:wght@300;400;600;700&display=swap">
<style>
  :root {
    --page-bg: #d9dad9;
    --card-bg: #e4e5e4;
    --ink: #111111;
    --ink-soft: #2a2a2a;
    --back-mark: #d2d3d2;
  }
  * { margin: 0; padding: 0; box-sizing: border-box; }
  html, body { width: 1200px; height: 780px; overflow: hidden; }
  body {
    background: var(--page-bg);
    font-family: "Poppins", sans-serif;
    color: var(--ink);
    position: relative;
  }
  .card {
    position: absolute;
    top: 236px;
    width: 520px;
    height: 300px;
    background: var(--card-bg);
  }
  .card--front { left: 50px; }
  .card--back { left: 630px; }

  /* Front */
  .brand {
    position: absolute;
    left: 30px;
    top: 34px;
    display: flex;
    align-items: center;
    gap: 10px;
  }
  .brand__square {
    width: 22px;
    height: 22px;
    border: 4px solid var(--ink);
    border-radius: 3px;
  }
  .brand__name {
    font-weight: 600;
    font-size: 17px;
    letter-spacing: 0.04em;
    text-transform: uppercase;
  }
  .person {
    position: absolute;
    right: 34px;
    top: 30px;
    text-align: right;
  }
  .person__name { font-size: 27px; line-height: 1.1; }
  .person__first { font-weight: 700; }
  .person__last { font-weight: 300; }
  .person__title { font-size: 13px; font-weight: 400; margin-top: 2px; }
  .accent-bar {
    position: absolute;
    right: 0;
    top: 30px;
    width: 14px;
    height: 56px;
    background: var(--ink);
  }
  .contact {
    position: absolute;
    left: 30px;
    bottom: 28px;
    font-size: 14px;
    line-height: 1.45;
    color: var(--ink-soft);
  }
  .contact__address { margin-bottom: 12px; }
  .contact__row { display: flex; align-items: center; gap: 10px; }
  .contact__icon { width: 14px; height: 14px; flex: none; }

  /* Back */
  .back-mark {
    position: absolute;
    inset: 0;
    display: flex;
    align-items: center;
    justify-content: center;
    gap: 14px;
  }
  .back-mark__square {
    width: 34px;
    height: 34px;
    border: 6px solid var(--back-mark);
    border-radius: 4px;
  }
  .back-mark__name {
    font-weight: 600;
    font-size: 26px;
    letter-spacing: 0.04em;
    text-transform: uppercase;
    color: var(--back-mark);
  }
</style>
</head>
<body>
  <section class="card card--front">
    <div class="brand">
      <span class="brand__square"></span>
      <span class="brand__name">Cedar Ridge Mechanical</span>
    </div>

    <div class="accent-bar"></div>
    <div class="person">
      <p class="person__name"><span class="person__first">Marta</span> <span class="person__last">Novak</span></p>
      <p class="person__title">Founder &amp; CEO</p>
    </div>

    <div class="contact">
      <p class="contact__address">1840 Harbor Line Rd. Suite 310<br>Tacoma, WA 98402</p>
      <p class="contact__row">
        <svg class="contact__icon" viewBox="0 0 16 16" aria-hidden="true"><path d="M3.5 1.5l2.5 3-1.5 1.5c.8 1.8 2.2 3.2 4 4L10 8.5l3 2.5-1.5 2.5C7 13 3 9 2.5 4z" fill="#111"/></svg>
        (555) 214-6039
      </p>
      <p class="contact__row">
        <svg class="contact__icon" viewBox="0 0 16 16" aria-hidden="true"><rect x="1" y="3" width="14" height="10" rx="1" fill="#111"/><path d="M1.5 3.5L8 9l6.5-5.5" stroke="#e4e5e4" stroke-width="1.3" fill="none"/></svg>
        info@cedarridgemech.com
      </p>
      <p class="contact__row">
        <svg class="contact__icon" viewBox="0 0 16 16" aria-hidden="true"><circle cx="8" cy="8" r="7" fill="#111"/><path d="M1 8h14M8 1c-3 3-3 11 0 14M8 1c3 3 3 11 0 14" stroke="#e4e5e4" stroke-width="1" fill="none"/></svg>
        www.cedarridgemech.com
      </p>
    </div>
  </section>

  <section class="card card--back">
    <div class="back-mark">
      <span class="back-mark__square"></span>
      <span class="back-mark__name">Cedar Ridge Mechanical</span>
    </div>
  </section>
</body>
</html>
```